Im open to ideas.. I was thinking on my business cards aswell as my logo. a place for my name. email. phone number and abn..

ive attched a file with my business logo. which i dont love the colours.. i was think a dark background with charcoal letters so something along those colour schumes but im open to ideas..

BRM Constructions

```html
<!DOCTYPE html>
<html lang="en">
<head>
<meta charset="utf-8">
<title>BRM Constructions – Business Card</title>
<link rel="stylesheet" href="https://fonts.googleapis.com/css2?family=Roboto:wght@400;500;700&display=swap">
<style>
  :root {
    --page-bg: #e9e7e4;
    --card-white: #ffffff;
    --brand-red: #ed1c24;
    --charcoal: #231f20;
    --text-light: #ffffff;
  }
  * { margin: 0; padding: 0; box-sizing: border-box; }
  html, body {
    width: 1200px;
    height: 987px;
    overflow: hidden;
    background: var(--page-bg);
    font-family: "Roboto", Arial, sans-serif;
  }
  .canvas {
    position: relative;
    width: 1200px;
    height: 987px;
  }
  .card {
    position: absolute;
    left: 306px;
    width: 615px;
    height: 350px;
    overflow: hidden;
    box-shadow: 0 2px 6px rgba(0,0,0,0.18);
  }
  .card-front { top: 130px; background: var(--card-white); }
  .card-back  { top: 506px; background: var(--brand-red); }

  .front-wordmark {
    position: absolute;
    right: 52px;
    top: 82px;
    font-weight: 700;
    font-size: 34px;
    color: var(--charcoal);
    letter-spacing: 1px;
  }
  .front-band {
    position: absolute;
    left: 0;
    right: 0;
    top: 226px;
    bottom: 0;
    background: var(--charcoal);
    border-top: 14px solid var(--brand-red);
  }
  .contact-list {
    position: absolute;
    left: 65px;
    top: 24px;
    list-style: none;
    color: var(--text-light);
    font-size: 15px;
  }
  .contact-list li {
    display: flex;
    align-items: center;
    height: 25px;
  }
  .contact-list li.abn { margin-bottom: 4px; }
  .contact-list svg { width: 15px; height: 15px; margin-right: 13px; fill: var(--text-light); }
  .holder {
    position: absolute;
    right: 42px;
    top: 36px;
    text-align: right;
    color: var(--text-light);
  }
  .holder-name { font-size: 20px; font-weight: 500; line-height: 1.2; }
  .holder-role { font-size: 17px; font-weight: 400; line-height: 1.3; }

  .back-wordmark {
    position: absolute;
    left: 0;
    right: 0;
    top: 158px;
    text-align: center;
    font-weight: 700;
    font-size: 44px;
    color: var(--text-light);
    letter-spacing: 1px;
  }
  .back-website {
    position: absolute;
    left: 0;
    right: 0;
    top: 294px;
    text-align: center;
    font-size: 14px;
    letter-spacing: 6px;
    color: var(--text-light);
  }
</style>
</head>
<body>
<main class="canvas">
  <section class="card card-front" aria-label="Business card front">
    <div class="front-wordmark">BRM Constructions</div>
    <div class="front-band">
      <ul class="contact-list">
        <li class="abn">ABN: 123456789</li>
        <li>
          <svg viewBox="0 0 16 16" aria-hidden="true"><path d="M1 5c0-2 3-3 7-3s7 1 7 3v1h-3V4.5C11 4 9.5 4 8 4S5 4 4 4.5V6H1z M4 7h8l2 7H2z M6 9.5a2 2 0 1 0 4 0a2 2 0 1 0-4 0z"/></svg>
          555 0142 7788
        </li>
        <li>
          <svg viewBox="0 0 16 16" aria-hidden="true"><path d="M1 3h14v1.2L8 9 1 4.2z M1 6l7 4.8L15 6v7H1z"/></svg>
          sam@brmbuild.com
        </li>
      </ul>
      <div class="holder">
        <p class="holder-name">Sam Carter</p>
        <p class="holder-role">President</p>
      </div>
    </div>
  </section>

  <section class="card card-back" aria-label="Business card back">
    <div class="back-wordmark">BRM Constructions</div>
    <div class="back-website">www.brmbuild.com</div>
  </section>
</main>
</body>
</html>
```